Business Card Design for ReaL ESTATE AGENT

New Business Cards for a real estate agent in Jacksonville, FL. My specialty is urban core, historic districts but sell through out the city. Company Name is Ninth and Crest Realty a division of the Dunholt Companies. The card needs to convey an essence of professionalism, knowledge and success.

Target Market(s)

Home buyers and Sellers

Industry/Entity Type

Real Estate

Contact Information for Business Card

Double sided

Font styles to use
Sans Serif

Requirements
Must have
• My logs and photo (provided). My contact information as follows:
• Owen Talbrick
• Cell 904-555-0183
• Office 904-555-0147
• Email owentalbrick@mailbrook.example
Nice to have
• Tag Line - Exceptional Effort. Proven Results.

```html
<!DOCTYPE html>
<html lang="en">
<head>
<meta charset="utf-8">
<title>Ninth and Crest Realty — Business Card</title>
<link rel="stylesheet" href="https://fonts.googleapis.com/css2?family=Montserrat:wght@400;500;600&display=swap">
<style>
  :root {
    --backdrop: #3b3532;
    --card-black: #1b1b1b;
    --accent: #ee4f3b;
    --accent-green: #2e7a4f;
    --text-light: #f4f4f4;
    --photo-dark: #2a2a2c;
    --photo-mid: #4a4442;
  }
  * { margin: 0; padding: 0; box-sizing: border-box; }
  html, body {
    width: 1200px;
    height: 844px;
    overflow: hidden;
    background: var(--backdrop);
    font-family: "Montserrat", sans-serif;
  }
  .stage {
    position: relative;
    width: 1200px;
    height: 844px;
  }
  .card {
    position: absolute;
    top: 268px;
    width: 540px;
    height: 309px;
    background: var(--card-black);
    overflow: hidden;
    box-shadow: 0 10px 28px rgba(0,0,0,0.45);
  }
  /* Front side */
  .card-front { left: 40px; }
  .band {
    position: absolute;
    left: 0;
    width: 100%;
    height: 14px;
    background: var(--accent);
  }
  .band-top { top: 0; }
  .band-bottom { bottom: 0; }
  .portrait {
    position: absolute;
    right: 0;
    top: 14px;
    bottom: 14px;
    width: 218px;
    background: radial-gradient(ellipse at 55% 40%, var(--photo-mid) 0%, var(--photo-dark) 70%);
  }
  .identity {
    position: absolute;
    left: 40px;
    top: 104px;
  }
  .agent-name {
    color: var(--accent);
    font-weight: 500;
    font-size: 19px;
    letter-spacing: 0.5px;
    padding-bottom: 5px;
    border-bottom: 1px solid var(--accent);
    display: inline-block;
  }
  .agent-title {
    color: var(--text-light);
    font-size: 14px;
    margin-top: 6px;
    margin-left: 30px;
  }
  .contact {
    position: absolute;
    left: 30px;
    width: 280px;
    top: 206px;
    text-align: center;
    color: var(--text-light);
    font-size: 14px;
    line-height: 24px;
    white-space: nowrap;
  }
  /* Back side */
  .card-back { left: 620px; }
  .edge-tab {
    position: absolute;
    width: 22px;
    height: 40px;
    background: var(--accent);
  }
  .edge-tab::after {
    content: "";
    position: absolute;
    top: 0;
    width: 3px;
    height: 100%;
    background: var(--accent-green);
  }
  .edge-tab-right { right: 0; top: 34px; }
  .edge-tab-right::after { left: 0; }
  .edge-tab-left { left: 0; top: 180px; }
  .edge-tab-left::after { right: 0; }
  .brand {
    position: absolute;
    inset: 0;
    display: flex;
    align-items: center;
    justify-content: center;
    gap: 14px;
  }
  .brand-mark {
    width: 16px;
    height: 16px;
    background: var(--accent);
  }
  .brand-name {
    color: var(--accent);
    font-weight: 600;
    font-size: 26px;
    letter-spacing: 1px;
    text-transform: uppercase;
  }
</style>
</head>
<body>
<main class="stage">
  <section class="card card-front">
    <div class="band band-top"></div>
    <div class="portrait" role="img" aria-label="Portrait photo of the agent in a suit and red tie"></div>
    <div class="identity">
      <div class="agent-name">OWEN TALBRICK</div>
      <div class="agent-title">Managing Director</div>
    </div>
    <div class="contact">
      <div class="contact-phone">904-555-0183</div>
      <div class="contact-email">owentalbrick@mailbrook.example</div>
    </div>
    <div class="band band-bottom"></div>
  </section>

  <section class="card card-back">
    <div class="edge-tab edge-tab-right"></div>
    <div class="edge-tab edge-tab-left"></div>
    <div class="brand">
      <span class="brand-mark"></span>
      <span class="brand-name">Ninth and Crest Realty</span>
    </div>
  </section>
</main>
</body>
</html>
```